Last of Tides

Story is a sequel to "Dusk of Copper Rain" which was a trip of an old ship with that name to India at the end of the Flower Power Era. This story is the aftermath of its eventual end in the scrapyard of Formosa. It describes the rather wild return trip of the motley crew from India via |Formosa back to the US with the dramatic undertone that the maritime industry is changing from the traditional break-bulk cargo transport to the modern method of container transport. The plot also involves a heist of thousands of bottles of whisky but that is of lesser concern. Design should be simple, be in the same style (with the original design of a single wilting flower on a beach) to affect its relation to the first book.The last of tides really signiies the end of traditional break-bulk (piecemeal) cargoship transport that had been done for thousands of years.

Target Market(s)

Young Adults and anyone associated with the Maritime Industry

Industry/Entity Type

Maritime industry

Font styles to use
Serif
Sans Serif
Other font styles liked:
• Arial or similar for the title; Serif for Author's name and text on back

Requirements
Must have
• Association with the first book design. Simple but effective design; subdued color scheme
Nice to have
• Totally wilted flower(s); deserted beach; sinking (dargo) ship (1960's); Sea;
Should not have
• Faces and pictures of personns, no complicated designs with lots of detail reflecting the plot; no bright colors

```html
<!DOCTYPE html>
<html lang="en">
<head>
<meta charset="utf-8">
<title>Last of Tides — Book Cover</title>
<link rel="stylesheet" href="https://fonts.googleapis.com/css2?family=Tenor+Sans&family=Cormorant+Garamond:ital,wght@0,600;1,500&display=swap">
<style>
  :root {
    --sky-light: #5ea6a5;
    --sky-mid: #3d8789;
    --sky-dark: #2c6a72;
    --hull-light: #8fb3ae;
    --hull-mid: #5f8d8c;
    --waterline: #3f98a3;
    --sea-mid: #1b5668;
    --sea-deep: #0c3045;
    --type: #ffffff;
    --type-edge: #0b1a1c;
  }
  * { margin: 0; padding: 0; box-sizing: border-box; }
  html, body {
    width: 800px;
    height: 1200px;
    overflow: hidden;
    background: var(--sea-deep);
  }
  .cover {
    position: relative;
    width: 800px;
    height: 1200px;
    overflow: hidden;
  }
  .cover-art {
    position: absolute;
    inset: 0;
    width: 800px;
    height: 1200px;
    display: block;
  }
  .title {
    position: absolute;
    inset: 0 0 auto 0;
    text-align: center;
    color: var(--type);
    text-shadow: 2px 2px 0 var(--type-edge);
    font-weight: 400;
  }
  .title-line {
    position: absolute;
    left: 0;
    right: 0;
    font-family: "Tenor Sans", Arial, sans-serif;
    line-height: 1;
  }
  .title-line--first {
    top: 84px;
    font-size: 146px;
    letter-spacing: 22px;
    padding-left: 22px;
  }
  .title-joiner {
    position: absolute;
    left: 0;
    right: 0;
    top: 226px;
    font-family: "Cormorant Garamond", serif;
    font-style: italic;
    font-weight: 500;
    font-size: 100px;
    line-height: 1;
  }
  .title-line--second {
    top: 336px;
    font-size: 146px;
    letter-spacing: 16px;
    padding-left: 16px;
  }
  .author {
    position: absolute;
    left: 0;
    right: 0;
    top: 1080px;
    text-align: center;
    font-family: "Cormorant Garamond", serif;
    font-weight: 600;
    font-size: 44px;
    letter-spacing: 14px;
    padding-left: 14px;
    color: var(--type);
    text-shadow: 1px 1px 0 var(--type-edge);
    line-height: 1;
  }
</style>
</head>
<body>
<main class="cover">
  <svg class="cover-art" viewBox="0 0 800 1200" role="img" aria-label="Stormy teal sky over a rough sea, with a rusted 1960s cargo ship sinking at an angle; its broken hull shows beneath the waterline">
    <defs>
      <linearGradient id="scene" x1="0" y1="0" x2="0" y2="1">
        <stop offset="0" stop-color="var(--sky-mid)"/>
        <stop offset="0.22" stop-color="var(--sky-light)"/>
        <stop offset="0.4" stop-color="var(--sky-dark)"/>
        <stop offset="0.48" stop-color="var(--hull-mid)"/>
        <stop offset="0.55" stop-color="var(--hull-light)"/>
        <stop offset="0.6" stop-color="var(--waterline)"/>
        <stop offset="0.75" stop-color="var(--sea-mid)"/>
        <stop offset="1" stop-color="var(--sea-deep)"/>
      </linearGradient>
    </defs>
    <rect class="scene" x="0" y="0" width="800" height="1200" fill="url(#scene)"/>
  </svg>

  <h1 class="title">
    <span class="title-line title-line--first">LAST</span>
    <span class="title-joiner">of</span>
    <span class="title-line title-line--second">TIDES</span>
  </h1>

  <p class="author">JAN VELDKAMP</p>
</main>
</body>
</html>
```